Book Title: “Faith: Road of Endless Grace” Please see the attachment “Text on the cover”.

Book Cover Design Instructions: This book is meant for people of all religions and nationalities. Therefore, on the cover, there should be no mosque or an object specific to any religion. The primary emphasis should be on the "unconditional love of God." Therefore, use universal symbols of love. The second priority themes could be Sufism, Peace, and self-improvement. Rest is your imagination. Please also see the attachment: 'Book description and author's Bio.'
This book has the potential to be a best seller. Please do a good job.
What Book Cover Formats are required: A designer should submit cover designs in three formats: (1) eBook, (2) Paperback, and (3) Hardback. These books will be published on Borvex QPL.
Format requirements for eBooks are available from: https://qpl.borvex.example/en_US/help/topic/R731928457.
You can find paperback and hardback cover measurements from: https://qpl.borvex.example/en_US/cover-calculator
• To complete the project, all three formats should be accepted by Borvex QPL.
• The book interior trim size is 6.14 X 9.21 inches.
• Interior Type: Premium color.
• No bleed.
• I do not upload barcode. So, the back cover should have room for Borvex to print the barcode.
• Number of pages 126.
Compensation for the designer: After selecting one designer, I will increase the amount by $200 on Artvelle to compensate for three deliverables.
Follow-up of the Project:
After the book is published, I may need minor revisions. For example, the number of pages may change. Therefore, I will need the same design in revised sizes. In that case, I will pay $25 for each revision. For example, if the number of pages changes, I will need a different spine for paperback and hardback, then I will pay the artist $25 + $25 = $50 for both designs.
List of Enclosers:
1. Text on the cover.
2. Book description and author's Bio for the back cover.
3. Later, I will upload my picture for the book's back cover.

Target Market(s)

Any adult

Industry/Entity Type

Any industry

Requirements
Must have
• Three Deliverables

```html
<!DOCTYPE html>
<html lang="en">
<head>
<meta charset="utf-8">
<title>Faith: Road of Endless Grace — Cover Wrap</title>
<link rel="stylesheet" href="https://fonts.googleapis.com/css2?family=Oswald:wght@200;300;400&family=Lato:wght@400;700&display=swap">
<style>
  :root {
    --page-bg: #ececec;
    --cover-green: #0e4843;
    --cover-green-deep: #0a3b37;
    --gold: #d8b36a;
    --gold-soft: #f0d9a3;
    --cream: #f6f0e2;
    --text-light: #e9efe9;
    --barcode-box: #ffffff;
  }
  * { margin: 0; padding: 0; box-sizing: border-box; }
  html, body {
    width: 837px; height: 1200px; overflow: hidden;
    background: var(--page-bg);
  }
  .cover-wrap {
    position: absolute;
    left: 18px; top: 311px;
    width: 800px; height: 577px;
    display: flex;
    background: var(--cover-green);
    box-shadow: 0 2px 8px rgba(0,0,0,0.18);
  }
  .back-cover {
    position: relative;
    width: 385px; height: 100%;
    padding: 26px 26px 0 26px;
    font-family: "Lato", sans-serif;
    color: var(--text-light);
  }
  .back-title {
    font-size: 15px; font-weight: 700; color: var(--gold);
  }
  .back-subtitle {
    font-size: 9.5px; color: var(--gold-soft); margin: 3px 0 12px;
  }
  .back-body p, .question-list li {
    font-size: 7px; line-height: 1.5;
  }
  .back-body p { margin-bottom: 8px; }
  .questions-heading { font-weight: 700; color: var(--cream); margin-bottom: 3px !important; }
  .question-list { list-style: decimal; padding-left: 14px; margin-bottom: 9px; }
  .author-bio { margin-top: 14px; }
  .bio-name { font-size: 8px; font-weight: 700; color: var(--gold); margin-bottom: 2px; }
  .barcode-space {
    position: absolute; right: 26px; bottom: 26px;
    width: 92px; height: 56px; background: var(--barcode-box);
  }
  .spine {
    position: relative;
    width: 30px; height: 100%;
    background: var(--cover-green-deep);
    border-left: 1px solid rgba(216,179,106,0.25);
    border-right: 1px solid rgba(216,179,106,0.25);
  }
  .spine-title, .spine-author {
    position: absolute; left: 50%;
    writing-mode: vertical-rl;
    transform: translateX(-50%);
    font-family: "Oswald", sans-serif;
    white-space: nowrap;
  }
  .spine-title { top: 28px; font-size: 11px; letter-spacing: 1.5px; color: var(--cream); font-weight: 300; }
  .spine-author { bottom: 24px; font-size: 9px; color: var(--gold); }
  .front-cover {
    position: relative;
    width: 385px; height: 100%;
    text-align: center;
  }
  .front-title {
    position: absolute; top: 54px; left: 0; right: 0;
    font-family: "Oswald", sans-serif;
    font-weight: 200;
    font-size: 96px; line-height: 1;
    letter-spacing: 6px;
    color: var(--cream);
  }
  .front-subtitle {
    position: absolute; top: 160px; left: 0; right: 0;
    font-family: "Oswald", sans-serif;
    font-weight: 300;
    font-size: 22px; letter-spacing: 2.5px;
    color: var(--gold);
  }
  .emblem-area {
    position: absolute; left: 82px; top: 262px;
    width: 220px; height: 150px;
  }
  .front-author {
    position: absolute; bottom: 44px; left: 0; right: 0;
    font-family: "Oswald", sans-serif;
    font-weight: 300;
    font-size: 20px; letter-spacing: 1px;
    color: var(--gold);
  }
</style>
</head>
<body>
  <main class="cover-wrap">
    <section class="back-cover">
      <h2 class="back-title">Faith: Road of Endless Grace</h2>
      <p class="back-subtitle">Guide to Cultivating Inner Peace and Mindful Living</p>
      <div class="back-body">
        <p>This gentle volume explores the timeless teachings of love found at the heart of faith, offering readers from every background a clear and warm path toward inner calm, deeper purpose and a more compassionate way of living each day.</p>
        <p class="questions-heading">This book addresses the following critical questions:</p>
        <ol class="question-list">
          <li>How can we feel the love of God in daily life?</li>
          <li>What does it mean to find peace within ourselves?</li>
          <li>How do kindness and patience shape a spiritual life?</li>
          <li>Why does mindful living bring us closer to grace?</li>
          <li>What simple practices help us grow in love and peace?</li>
        </ol>
        <p>Drawing on classic wisdom and modern insight, the author guides readers step by step toward a life rooted in gratitude, humility and service.</p>
        <p>Written for people of all faiths, this book invites you to open your heart and walk the road of endless grace.</p>
        <div class="author-bio">
          <p class="bio-name">Dr. Naveen Corrall</p>
          <p>Dr. Corrall holds degrees in physics and computer science and has spent many years teaching, writing and speaking about love, peace and mindful living.</p>
        </div>
      </div>
      <div class="barcode-space"></div>
    </section>

    <section class="spine">
      <span class="spine-title">FAITH &nbsp;ROAD OF ENDLESS GRACE</span>
      <span class="spine-author">Dr. Naveen Corrall</span>
    </section>

    <section class="front-cover">
      <h1 class="front-title">FAITH</h1>
      <p class="front-subtitle">ROAD OF ENDLESS GRACE</p>
      <svg class="emblem-area" viewBox="0 0 220 150" role="img" aria-label="Golden emblem of an infinity loop joined with a heart, symbol of endless love">
        <defs>
          <radialGradient id="emblemGlow" cx="50%" cy="50%" r="50%">
            <stop offset="0%" stop-color="#e6c37c" stop-opacity="0.85"/>
            <stop offset="60%" stop-color="#c99f55" stop-opacity="0.35"/>
            <stop offset="100%" stop-color="#0e4843" stop-opacity="0"/>
          </radialGradient>
        </defs>
        <rect x="0" y="0" width="220" height="150" rx="40" fill="url(#emblemGlow)"/>
      </svg>
      <p class="front-author">Dr. Naveen Corrall</p>
    </section>
  </main>
</body>
</html>
```